Christmas Collection Candle Label Design

Looking to update our existing Christmas Candle Collection labels. Labels should reflect the overall feel of our brand- www.kelvanoro.ca
Want to include some color elements. Holiday colors added into design but more muted/ earthy tones not vibrant colors . Metallic elements and line art botanical illustration. Fonts should be more align to brand
Scents
Holiday Tree
Candy Cane
Sugar and Spice
Joyeaux Noel

```html
<!DOCTYPE html>
<html lang="en">
<head>
<meta charset="utf-8">
<title>Kelvanoro – Candy Cane Candle Label</title>
<link rel="stylesheet" href="https://fonts.googleapis.com/css2?family=Poppins:wght@400;500&family=Sofia&display=swap">
<style>
  :root {
    --backdrop: #e6e6e6;
    --label-tan: #e0d6b8;
    --label-white: #ffffff;
    --ink-dark: #1f1e1c;
    --ink-grey: #5a5a5a;
    --divider-grey: #8a8a8a;
    --botanical-light: #fbfbfb;
    --botanical-mid: #ececec;
  }
  html, body {
    margin: 0;
    padding: 0;
    width: 730px;
    height: 1200px;
    overflow: hidden;
    background: var(--backdrop);
  }
  .canvas {
    width: 730px;
    height: 1200px;
    display: flex;
    align-items: center;
    justify-content: center;
  }
  .candle-label {
    width: 640px;
    height: 540px;
    display: block;
    box-shadow: 0 6px 10px rgba(0, 0, 0, 0.18);
  }
  .brand-name {
    font-family: "Poppins", sans-serif;
    font-weight: 500;
    font-size: 52px;
    letter-spacing: 1px;
    fill: var(--ink-dark);
  }
  .brand-tagline {
    font-family: "Poppins", sans-serif;
    font-weight: 500;
    font-size: 13px;
    letter-spacing: 4.5px;
    fill: var(--ink-dark);
  }
  .scent-name {
    font-family: "Sofia", cursive;
    font-size: 132px;
    fill: var(--label-white);
  }
  .scent-subline {
    font-family: "Poppins", sans-serif;
    font-weight: 400;
    font-size: 35px;
    fill: var(--ink-dark);
  }
  .footer-info {
    font-family: "Poppins", sans-serif;
    font-weight: 400;
    font-size: 32px;
    fill: var(--ink-grey);
  }
  .footer-divider {
    stroke: var(--divider-grey);
    stroke-width: 1.5;
  }
</style>
</head>
<body>
<main class="canvas">
  <svg class="candle-label" viewBox="0 0 994 838" xmlns="http://www.w3.org/2000/svg" aria-label="Candy Cane candle label">
    <defs>
      <radialGradient id="botanical-fill" cx="0.5" cy="0.65" r="0.75">
        <stop offset="0" stop-color="var(--botanical-light)"/>
        <stop offset="1" stop-color="var(--botanical-mid)"/>
      </radialGradient>
    </defs>

    <rect class="label-base" x="0" y="0" width="994" height="838" fill="var(--label-white)"/>

    <path class="botanical-area" role="img" aria-label="Faint grey line-art botanical illustration of blossoms, buds and branches"
          d="M0 405 Q497 667 994 405 V773 H0 Z" fill="url(#botanical-fill)"/>

    <path class="header-panel" d="M0 0 H994 V383 Q497 663 0 383 Z" fill="var(--label-tan)"/>
    <path class="header-rule" d="M0 405 Q497 667 994 405" fill="none" stroke="var(--label-tan)" stroke-width="7"/>

    <text class="brand-name" x="497" y="138" text-anchor="middle">KELVANORO</text>
    <text class="brand-tagline" x="497" y="160" text-anchor="middle">PURE PLANT BASED SCENTS</text>

    <text class="scent-name" x="497" y="333" text-anchor="middle">Candy Cane</text>
    <text class="scent-subline" x="497" y="443" text-anchor="middle">Made with plant based botanicals</text>

    <path class="footer-band" d="M0 789 Q0 773 16 773 H978 Q994 773 994 789 V838 H0 Z" fill="var(--label-tan)"/>
    <g class="footer-info-row">
      <text class="footer-info" x="456" y="817" text-anchor="middle" transform="translate(-253 0)">MADE IN CANADA</text>
      <line class="footer-divider" x1="368" y1="791" x2="368" y2="817"/>
      <text class="footer-info" x="489" y="817" text-anchor="middle">KELVANORO</text>
      <line class="footer-divider" x1="611" y1="791" x2="611" y2="817"/>
      <text class="footer-info" x="782" y="817" text-anchor="middle">Net WT. 10oz/283g</text>
    </g>
  </svg>
</main>
</body>
</html>
```